Maple Beacon Website

We are starting a marketing company and to do that we need a website! We want a website that will inspire and persuade to bring out the awesomeness in our clients.
What we want to see:
- Inspirational and persuasive imagery that relate to Branding.
- No cliche images eg. business man, suits and hand shakes
- We want to transform and educate our clients.
- We want to show them the path and would like our website to really act as a guide that guides them step by step through our process.
- We want the portray that we are an investment but not have a pretentious way to it. We put our heart into every project and that is how we treat our clients.
-When you submit your design please include what platform you have created for. Preference would be Wordpress or Joobla.

We have included the psd file for the wire frame, logo files, font files, site map and a link to a video we create to give you more information on what we would like to see. http://clipvault.example/t/qk82LmZpr

Feel free to make small modification to the logos if you think it will improve it. Your creativity and advice is most welcome.
Updates

One thing we forgot. We would like to have our contact information near the top of the website as well as at the bottom.  Here is out contact info:

Email: info@maplebeacon.example
Phone: 587-555-0142

Project Deadline Extended
Reason: As we are new with the platform and that we want to optimize our results, we decided to extend the deadline by 15 days. Thanks!

Target Market(s)

28-60, Male and Female, Oil field, Local Businesses, Dentists, Chiropractors, Hair salon, Construction/Renovation, Events etc

Industry/Entity Type

Investment

Requirements
Must have
• - 4 Inspirational and persuasive Imagery for the top portion of the website
- Must have a feel as if your not on a website an example of this is linked below.
http://www.artbidhub.example/design/402957/web-design-by-lena-torvik
Nice to have
• - Creative advice from you.
- Creative buttons for Get Free Quote and Subscribe buttons. Something out of the box that draws peoples attention. eg. a 'B' button. Just and example but still something related to branding.
Should not have
• No Cliches

```html
<!DOCTYPE html>
<html lang="en">
<head>
<meta charset="utf-8">
<title>Maple Beacon</title>
<link rel="stylesheet" href="https://fonts.googleapis.com/css2?family=Alfa+Slab+One&family=Arvo:wght@700&family=Luckiest+Guy&family=Marcellus&family=PT+Sans+Narrow&family=Open+Sans:ital,wght@1,600&family=Arimo:wght@400;700&family=Playfair+Display:ital,wght@1,700&display=swap">
<style>
:root{
  --green:#5a9a22;
  --green-light:#8cc63e;
  --green-dark:#3f7a16;
  --gray:#666;
  --gray-light:#b3b3b3;
  --text:#7a7a7a;
  --panel:#ececec;
  --white:#fff;
}
*{margin:0;padding:0;box-sizing:border-box}
html,body{width:1200px;height:953px;overflow:hidden}
body{position:relative;background:linear-gradient(#f4f4f4 0,#fff 460px);font-family:Arimo,Arial,sans-serif}
.abs{position:absolute}

.logo-box{left:35px;top:0;width:283px;height:139px;background:var(--white)}
.logo-name{position:absolute;left:22px;top:40px;display:flex;align-items:center;gap:10px;font-family:Arvo,serif;font-weight:700;font-size:29px;color:var(--gray);white-space:nowrap}
.logo-mark{width:20px;height:20px;background:var(--green-light)}
.tagline{position:absolute;left:0;width:100%;top:114px;text-align:center;font-family:"Open Sans",sans-serif;font-style:italic;font-weight:600;font-size:15px;color:#444;white-space:nowrap}

.side-nav{left:35px;top:139px;width:283px;height:235px;background:linear-gradient(90deg,#fff,#e8e8e8)}
.side-nav ul{list-style:none;position:absolute;left:24px;top:28px}
.side-nav li{font-family:"PT Sans Narrow",sans-serif;font-size:21px;line-height:28.5px;color:#222}
.connect{position:absolute;left:0;width:100%;top:198px;text-align:center;font-family:"Luckiest Guy","Arial Black",sans-serif;font-size:24px;color:#444;letter-spacing:.5px;white-space:nowrap}

.contact-top{top:24px;left:572px;display:flex;align-items:center;font-family:Arimo,Arial,sans-serif;font-weight:700;font-size:16px;color:#444;white-space:nowrap}
.contact-top .label{color:var(--green)}
.icon-circle{width:38px;height:38px;border-radius:50%;background:radial-gradient(circle at 40% 35%,#fff,#bbb);display:flex;align-items:center;justify-content:center;margin-right:10px}
.contact-top .sep{width:40px}
.top-rule{left:400px;top:66px;width:765px;height:1px;background:#ddd}

.steps{top:78px;left:398px;display:flex;font-family:"PT Sans Narrow",sans-serif;font-size:20px;color:var(--gray-light);white-space:nowrap}
.steps li{list-style:none;display:flex;align-items:center;margin-right:20px}
.steps li::before{content:"";width:17px;height:17px;border-radius:50%;background:#c8c8c8;margin-right:9px}
.steps li.active{color:var(--green-light)}
.steps li.active::before{background:radial-gradient(circle at 40% 35%,#b7e07a,var(--green))}

.banner{left:401px;top:119px;width:687px;height:235px;background:var(--panel);box-shadow:0 0 0 5px #fff}
.banner-art{position:absolute;left:45px;top:18px;width:420px;height:200px;border-radius:10px;background:linear-gradient(100deg,#d8383a 0,#e8c43a 25%,#3d9b3a 42%,#2f5fd0 60%,#f0a020 78%,#9b2fd0 100%);opacity:.85}
.banner-slogan{position:absolute;left:520px;width:150px;top:74px;text-align:center;font-family:Arvo,serif;font-weight:700;font-size:32px;line-height:42px}
.banner-slogan .be{color:var(--gray-light)}
.banner-slogan .unique{color:var(--green-light)}

.newsletter{left:35px;top:378px;width:1130px;height:51px;background:linear-gradient(var(--green-light),var(--green));box-shadow:0 0 0 3px #fff}
.social{position:absolute;top:8px;width:35px;height:35px;border-radius:4px;background:linear-gradient(#fff,#ddd)}
.newsletter-text{position:absolute;left:274px;top:13px;font-family:"Playfair Display",Georgia,serif;font-style:italic;font-weight:700;font-size:20px;color:var(--white);white-space:nowrap}
.subscribe-btn{position:absolute;left:760px;top:4px;width:157px;height:42px;border-radius:8px;background:linear-gradient(#fff,#e6e6e6);display:flex;align-items:center;justify-content:center;font-family:"Luckiest Guy","Arial Black",sans-serif;font-size:17px;color:var(--green-dark);letter-spacing:.3px;white-space:nowrap}

.welcome{left:0;width:1180px;top:468px;text-align:center;font-family:"Alfa Slab One",serif;font-size:26px;color:var(--gray);white-space:nowrap}
.welcome .accent{color:var(--green)}
.intro{left:284px;top:534px;width:660px;font-size:14px;line-height:21.2px;color:var(--text)}
.intro p+p{margin-top:21px}
.quote-btn{left:740px;top:738px;width:202px;height:43px;border-radius:7px;background:linear-gradient(#6dbb2c,var(--green-dark));box-shadow:0 3px 4px rgba(0,0,0,.3);display:flex;align-items:center;justify-content:center;gap:8px;font-family:Marcellus,serif;font-size:25px;color:var(--white);white-space:nowrap}

.footer{left:0;top:809px;width:1200px;height:144px;background:linear-gradient(#fff,#f2f2f2 60%,#fafafa)}
.footer-nav{position:absolute;top:49px;left:289px;display:flex;font-size:14px;color:#333;white-space:nowrap}
.footer-nav span.sep{margin:0 36px 0 26px}
.footer-contact{position:absolute;top:91px;left:287px;font-size:14px;color:var(--green);white-space:nowrap}
.footer-contact .copy{color:#444;margin-left:14px}
</style>
</head>
<body>
  <div class="abs logo-box">
    <div class="logo-name"><span class="logo-mark"></span>Maple Beacon</div>
    <div class="tagline">Because You´re Awesome!</div>
  </div>

  <nav class="abs side-nav">
    <ul>
      <li>STRATEGY</li><li>PORTFOLIO</li><li>ABOUT US</li><li>CONTACT US</li><li>BLOG</li>
    </ul>
    <div class="connect">Connect with us!</div>
  </nav>

  <div class="abs contact-top">
    <span class="icon-circle"><svg width="20" height="20" viewBox="0 0 20 20"><circle cx="10" cy="10" r="7.5" fill="none" stroke="#333" stroke-width="2"/><circle cx="10" cy="10" r="3" fill="none" stroke="#333" stroke-width="2"/></svg></span>
    <span class="label">Email:&nbsp;</span>info@maplebeacon.example
    <span class="sep"></span>
    <span class="icon-circle"><svg width="20" height="20" viewBox="0 0 20 20"><path d="M5 3l3 3-2 2c1 2.5 3.5 5 6 6l2-2 3 3-2 2C9 17 3 11 3 5z" fill="#333"/></svg></span>
    <span class="label">Phone:&nbsp;</span>587-555-0142
  </div>
  <div class="abs top-rule"></div>

  <ul class="abs steps">
    <li class="active">Maple Beacon</li><li>Be Found</li><li>Connect</li><li>Get Growing</li>
  </ul>

  <section class="abs banner">
    <div class="banner-art" role="img" aria-label="Colourful puzzle pieces spelling the word brand"></div>
    <div class="banner-slogan"><div class="be">BE</div><div class="unique">UNIQUE</div></div>
  </section>

  <section class="abs newsletter">
    <span class="social" style="left:50px"></span>
    <span class="social" style="left:102px"></span>
    <span class="social" style="left:155px"></span>
    <div class="newsletter-text">Get Tips and Tricks! Subscribe to our Newsletter.</div>
    <div class="subscribe-btn">SUBSCRIBE NOW</div>
  </section>

  <h1 class="abs welcome"><span class="accent">WELCOME TO</span> MAPLE BEACON</h1>
  <div class="abs intro">
    <p>This is just a bunch of words put toghether to make it look like  paragraph. It is purly for show and filler so that we can have a general idea of what it will ook like when we put in the proper pagaraphs thatmake up our mission statment. I think this font size looks pretty good but maybe be a tad bit smaler.  would like to see the welcome a little more dramatic looking. I think that</p>
    <p>is all I need to write here for now. This is just a bunch of words put toghether to make it look like  paragraph. It is purly for show and filler so that we can have a general idea of what it will ook like when we put in the proper pagaraphs thatmake up our mission statment. I think this font size looks pretty good but maybe be a tad bit smaler.  would like to see the welcome a little more dramatic looking. I think</p>
  </div>
  <div class="abs quote-btn">FREE QUOTE<svg width="12" height="16" viewBox="0 0 12 16"><path d="M0 0l12 8-12 8z" fill="#fff"/></svg></div>

  <footer class="abs footer">
    <div class="footer-nav">
      <span>Site Map</span><span class="sep">/</span>
      <span>Strategy</span><span class="sep">/</span>
      <span>Portfolio</span><span class="sep">/</span>
      <span>About Us</span><span class="sep">/</span>
      <span>Contact Us</span><span class="sep">/</span>
      <span>Blog</span>
    </div>
    <div class="footer-contact">Contact info &nbsp;: &nbsp;Email: info@maplebeacon.example &nbsp;&nbsp;&nbsp;&nbsp;Phone: 587-555-0142<span class="copy">©MAPLE BEACON INC. 2013</span></div>
  </footer>
</body>
</html>
```